Harborview Estates Business Card for Apartment Buildings

Create business cards for resident managers who run apartment buildings. The audience is the public who are searching for apartment rentals, and current residents who live at the apartment building. Key design element will be incorporating the company logo, however, the logo cannot dominate. The building name and manager name are more important than the logo. Current business card design leaves little room for copy, so we may need to reduce the size on the current card to allow for more space for copy.

Target Market(s)

Adults 18-65 years of age, who are looking for an apartment rental, plus current residents who live at our apartment buildings.

Industry/Entity Type

Property Management

Contact Information for Business Card

A major design element will be use of the company logo. Important property and manager contact information must be part of the design. The size of the logo will need to be reduced to make room for building and manager contact copy.

Font styles to use
Sans Serif

Colors
3176b5
000000
959595
ffffff

Requirements
Must have
• 1) Incorporate the company logo.
• 2) Use the company colors (dark blue, black/grey, over white).
• 3) FEATURE THE BUILDING NAME
• 4) FEATURE THE MANAGER NAME
• 5) The company name is less important than BUILDING and MANAGER
• 6) Manager contact information
• **SEE ATTACHED CREATIVE BRIEF**
Nice to have
• 1) Back of card logo watermark
• 2) Ability to write notes on back of carfd
Should not have
• Avoid letting the company logo dominate the card, the building name and manager are more important than the company logo.

```html
<!DOCTYPE html>
<html lang="en">
<head>
<meta charset="UTF-8">
<title>Harborview Estates – Resident Manager Card</title>
<link href="https://fonts.googleapis.com/css2?family=Roboto:wght@400;700&display=swap" rel="stylesheet">
<style>
  :root {
    --brand-blue: #0e6aa9;
    --text-grey: #3a3a3a;
    --soft-grey: #959595;
    --paper: #ffffff;
    --stage: #e9e9e9;
    --watermark: #e6e8ee;
  }
  * { margin: 0; padding: 0; box-sizing: border-box; }
  html, body {
    width: 1200px; height: 960px; overflow: hidden;
    background: var(--stage);
    font-family: "Roboto", Arial, sans-serif;
  }
  .canvas { position: relative; width: 1200px; height: 960px; }
  .card {
    position: absolute; left: 220px; width: 760px; height: 433px;
    background: var(--paper);
    box-shadow: 0 2px 6px rgba(0,0,0,0.18);
    overflow: hidden;
  }
  .card--front { top: 28px; }
  .card--back { top: 501px; }

  .manager-name {
    position: absolute; left: 68px; top: 64px;
    font-size: 24px; font-weight: 700; color: var(--brand-blue);
  }
  .manager-title {
    position: absolute; left: 68px; top: 96px;
    font-size: 17px; color: var(--text-grey);
  }
  .building-name {
    position: absolute; left: 68px; top: 154px;
    font-size: 16px; color: var(--brand-blue);
  }
  .address { position: absolute; left: 68px; top: 180px; font-size: 16px; color: var(--text-grey); line-height: 26px; }
  .contact-list { position: absolute; left: 68px; top: 256px; list-style: none; }
  .contact-list li {
    display: flex; align-items: center; height: 25.5px;
    font-size: 16.5px; color: var(--text-grey);
  }
  .contact-list svg { width: 17px; height: 17px; margin-right: 10px; fill: var(--brand-blue); }

  .email-band {
    position: absolute; left: 0; top: 356px; width: 574px; height: 28px;
    background: var(--brand-blue); color: var(--paper);
    font-size: 16px; line-height: 28px; padding-left: 68px;
  }
  .band-mark {
    position: absolute; left: 588px; top: 338px; width: 62px; height: 62px;
    border-radius: 50%; background: var(--brand-blue);
  }

  .company-name {
    position: absolute; right: 62px; top: 78px;
    display: flex; align-items: center; gap: 12px;
    font-size: 27px; font-weight: 700; color: var(--brand-blue);
    letter-spacing: 0.3px;
  }
  .company-name .dot { width: 40px; height: 40px; border-radius: 50%; background: var(--brand-blue); }

  .back-mark {
    position: absolute; inset: 0;
    display: flex; flex-direction: column; align-items: center; justify-content: center; gap: 22px;
  }
  .back-mark .dot { width: 190px; height: 190px; border-radius: 50%; background: var(--watermark); }
  .back-mark .name { font-size: 30px; font-weight: 700; color: var(--watermark); }
</style>
</head>
<body>
<div class="canvas">
  <section class="card card--front">
    <h1 class="manager-name">Delia Marquez</h1>
    <p class="manager-title">Resident Manager</p>
    <p class="building-name">Palm Court Apartments</p>
    <p class="address">2140 Juniper Avenue<br>Seacrest, CA 92071</p>
    <ul class="contact-list">
      <li><svg viewBox="0 0 24 24" aria-label="Phone"><path d="M17 2c-6 2-11 9-11 16 0 2 1 4 3 4l2-1-1-5-2 0c0-4 2-8 6-10l1 2 4-2z"/></svg>555-210-4471</li>
      <li><svg viewBox="0 0 24 24" aria-label="Fax"><path d="M3 9h18v11H3zM7 3h10v5H7zM6 12h3v2H6zm5 0h3v2h-3zm-5 4h3v2H6zm5 0h3v2h-3zm5-4h3v6h-3z"/></svg>555-210-4472</li>
      <li><svg viewBox="0 0 24 24" aria-label="Message"><path d="M2 5h20v14H2zm2 2v1l8 5 8-5V7l-8 5z"/></svg>555-210-4480</li>
    </ul>
    <div class="email-band">delia@harborviewest.com</div>
    <div class="band-mark"></div>
    <div class="company-name"><span class="dot"></span>Harborview Estates</div>
  </section>

  <section class="card card--back">
    <div class="back-mark">
      <span class="dot"></span>
      <span class="name">Harborview Estates</span>
    </div>
  </section>
</div>
</body>
</html>
```